Kelumo.cn needs pages to be re-designed

www.kelumo.cn is our current new site which was launched in April.
We're a financial services website in the crowdfunding space in China to connect borrower's and lender's.

test.kelumo.cn is our test site
u: test
p: newtest
http://test.kelumo.cn/
http://test.kelumo.cn/user/accounts/new_lender
http://test.kelumo.cn/user/accounts/new_borrower
http://test.kelumo.cn/introductions/protection
http://test.kelumo.cn/introductions
http://test.kelumo.cn/introductions/kelumo_admin
http://test.kelumo.cn/introductions/contact
Some of the pages have pop-ups in the bloc's of the pages. Please click the links, to see more content.

User's currently criticize the website for being:
- Too Western looking
- Too simple, too little content
- Content NOT in the pop-ups are too simple
- Pictures are too big and too much blank space
- Relevant information is not there when needed
- The pictures are too generic

What we would like to do is re-design those pages with the same color scheme and style to be more compelling, efficient, non-intimidating and easy-to-use. Our audience is Ages 25-35 predominantly male investors.
We are looking for more ideas to make the content match the style, while bridging western and chinese design. Our ultimate goal is to increase registrants to the website and highlight our core competitive advantages.

Some competitors websites are:
www.fobuxiqi.com
www.tamev.com
www.zzzlendo.com

Reason: Not enough good designs that follow the prompt. Same style, better information layout!

Reason: Still have not received a design we're satisfied with

Reason: WE DONT WANT A COMPLETE REDESIGN OF PAGES . KEEP THE EXACT SAME COLOR AND STYLE - WE WANT CONTENT RE-DESIGN! THE BLOCS ARE TOO SIMPLE - WE WANT MORE CONTENT INSIDE.

Reason: no new designs

Reason: no new designs

Reason: other non-registered pages need to be re-designed

```html
<!DOCTYPE html>
<html lang="zh-CN">
<head>
<meta charset="utf-8">
<title>Kelumo 合作伙伴</title>
<link rel="stylesheet" href="https://fonts.googleapis.com/css2?family=Noto+Sans+SC:wght@400;500;700&display=swap">
<style>
:root{
  --green:#5cb531;
  --blue:#3d8fd6;
  --ink:#333;
  --muted:#888;
  --line:#e3e3e3;
  --card:#fff;
  --logo-bg:#f0f0f0;
  --band:#3a3a3a;
  --news-bg:#ececec;
  --footer:#3b3b3b;
}
*{box-sizing:border-box;margin:0;padding:0}
html,body{width:1200px;height:3256px;overflow:hidden}
body{font-family:"Noto Sans SC",sans-serif;color:var(--ink);background:#fff;position:relative}
.brand{display:flex;align-items:center;gap:10px;font-weight:700;color:var(--green);font-size:22px}
.brand .dot{width:34px;height:34px;border-radius:50%;background:var(--green)}
.site-header{height:88px;display:flex;align-items:center;justify-content:space-between;padding:0 90px 0 100px}
.top-nav{display:flex;gap:34px;font-size:14px;color:#444}
.top-nav span{display:flex;align-items:center;gap:6px}
.top-nav svg{width:14px;height:14px}
.hero{position:absolute;top:88px;left:0;width:1200px;height:475px;background:linear-gradient(180deg,#cfd3d6 0%,#9ea4a8 45%,#6d7378 100%)}
.hero h1{position:absolute;bottom:30px;width:100%;text-align:center;color:#fff;font-size:34px;font-weight:500;letter-spacing:2px}
.hero .dots{position:absolute;top:22px;right:100px;display:flex;gap:6px}
.hero .dots i{width:9px;height:9px;border-radius:50%;background:#fff;opacity:.6}
.hero .dots i:first-child{opacity:1}
.tab-bar{position:absolute;top:563px;left:0;width:1200px;height:65px;background:var(--band);display:flex;justify-content:center}
.tab-bar a{width:210px;display:flex;align-items:center;justify-content:center;color:#fff;font-size:22px;text-decoration:none}
.tab-bar a.active{background:var(--green)}
.section-title{position:absolute;top:675px;left:128px;font-size:26px;color:var(--green);font-weight:500}
.partner-grid{position:absolute;top:728px;left:128px;width:944px;display:grid;grid-template-columns:repeat(3,310px);grid-template-rows:388px 378px 378px 378px 338px;gap:8px 7px}
.partner-card{background:var(--card);border:1px solid var(--line);text-align:center}
.partner-logo{height:156px;background:var(--logo-bg);display:flex;flex-direction:column;align-items:center;justify-content:center;gap:10px;font-size:20px;font-weight:700;color:#555}
.partner-logo .mark{width:22px;height:22px;border-radius:50%;background:#bbb;display:inline-block;vertical-align:middle;margin-right:8px}
.scale{background:var(--blue);color:#fff;font-size:15px;font-weight:700;padding:4px 0;width:240px}
.partner-card h3{font-size:15px;margin:22px 0 12px;font-weight:700}
.partner-card p{font-size:11.5px;line-height:1.75;color:var(--muted);padding:0 24px}
.more-btn{display:inline-block;margin-top:16px;background:var(--green);color:#fff;font-size:12px;padding:6px 28px;border-radius:14px}
.news{position:absolute;top:2680px;left:0;width:1200px;height:262px;display:flex}
.news-col{flex:1;background:var(--news-bg);padding:28px 0 0}
.news-col.left{padding-left:210px;background:#f0f0f0}
.news-col.right{padding-left:47px}
.news-col h2{font-size:26px;color:var(--green);font-weight:500;margin-bottom:12px}
.news-col ul{list-style:none;font-size:11.5px;line-height:26px;color:#333}
.news-col li::before{content:"";display:inline-block;width:5px;height:5px;background:#444;margin-right:10px;vertical-align:middle}
.news-col li.on{color:var(--green);text-decoration:underline}
.news-col li.on::before{background:var(--green)}
.pill{display:inline-block;margin-top:10px;background:#777;color:#fff;font-size:12px;padding:4px 22px;border-radius:14px}
.partner-strip{position:absolute;top:2948px;left:210px;width:800px}
.partner-strip h4{font-size:13px;font-weight:500;margin-bottom:8px}
.partner-strip div{display:flex;gap:34px;font-size:14px;font-weight:700;color:#666}
.site-footer{position:absolute;top:3028px;left:0;width:1200px;height:182px;background:var(--footer);color:#ddd;font-size:13px;padding:22px 0 0 175px}
.site-footer .row{display:flex;gap:18px;margin-bottom:14px;align-items:center}
.site-footer .circle{width:22px;height:22px;border-radius:50%;background:#888}
.chat{background:#222;border-radius:14px;padding:3px 18px}
.badges{display:flex;gap:24px;margin-top:10px}
.badges i{width:120px;height:30px;background:#f4f4f4;border-radius:2px;display:block}
.hotline{position:absolute;top:22px;right:175px;text-align:right}
.hotline b{display:block;font-size:32px;color:#fff;font-weight:700;letter-spacing:1px}
.hotline small{font-size:11px;color:#bbb}
.copyright{position:absolute;top:3210px;left:0;width:1200px;height:46px;display:flex;align-items:center;justify-content:space-between;padding:0 175px;font-size:11px;color:#999}
.copyright .brand{font-size:16px}
.copyright .brand .dot{width:22px;height:22px}
</style>
</head>
<body>
<header class="site-header">
  <div class="brand"><span class="dot"></span>Kelumo</div>
  <nav class="top-nav">
    <span><svg viewBox="0 0 14 14"><path d="M7 1l5 2v4c0 3-2 5-5 6-3-1-5-3-5-6V3z" fill="#555"/></svg>安全</span>
    <span><svg viewBox="0 0 14 14"><circle cx="7" cy="7" r="6" fill="#555"/></svg>投资</span>
    <span><svg viewBox="0 0 14 14"><rect x="2" y="2" width="10" height="11" fill="#555"/></svg>贷款</span>
    <span><svg viewBox="0 0 14 14"><rect x="2" y="6" width="10" height="7" fill="#555"/><path d="M4 6V4a3 3 0 016 0v2" stroke="#555" fill="none" stroke-width="1.5"/></svg>登录 ▾</span>
  </nav>
</header>

<section class="hero" role="img" aria-label="团队成员双手叠放在一起的合作照片">
  <div class="dots"><i></i><i></i><i></i><i></i></div>
  <h1>我們的合作夥伴</h1>
</section>

<nav class="tab-bar">
  <a>公司介绍</a><a>公司管理</a><a class="active">合作伙伴</a><a>加入我们</a><a>联系我们</a>
</nav>

<h2 class="section-title">合作伙伴</h2>

<main class="partner-grid">
  <article class="partner-card">
    <div class="partner-logo"><span><i class="mark"></i>青岚人寿</span><span class="scale">资产管理规模:超260亿</span></div>
    <h3>青岚人寿保险股份有限公司</h3>
    <p>青岚人寿保险股份有限公司是一家综合性人寿保险机构，服务网络遍及多个省市，为个人与家庭提供保障规划及资产管理服务，与本平台在风险保障领域开展长期合作。</p>
    <span class="more-btn">了解更多</span>
  </article>
  <article class="partner-card">
    <div class="partner-logo"><span><i class="mark"></i>朗峰保险经纪</span><span class="scale">资产管理规模:超80亿</span></div>
    <h3>朗峰(北京)保险经纪有限公司</h3>
    <p>朗峰(北京)保险经纪有限公司是一家专业保险经纪机构，为企业和个人提供风险评估、保险方案设计及理赔协助等服务，帮助客户更好地管理各类风险。</p>
    <span class="more-btn">了解更多</span>
  </article>
  <article class="partner-card">
    <div class="partner-logo"><span><i class="mark"></i>Trenholt Capital</span></div>
    <h3>Trenholt Capital</h3>
    <p>Trenholt Capital 是一家投资管理机构，专注于中小企业融资与直接贷款业务，拥有丰富的信贷经验和严谨的风控体系。</p>
  </article>

  <article class="partner-card">
    <div class="partner-logo"><span><i class="mark"></i>Orvane Partners</span></div>
    <h3>Orvane Partners</h3>
    <p>Orvane Partners 是一家专注于早期投资的机构，关注互联网、金融科技与消费领域，帮助优秀团队快速成长。</p>
  </article>
  <article class="partner-card">
    <div class="partner-logo"><span><i class="mark"></i>小微信贷同业会</span></div>
    <h3>小微信贷同业会</h3>
    <p>小微信贷同业会是由多家微型金融机构共同发起的行业组织，致力于推动普惠金融发展，促进行业自律与规范经营。</p>
  </article>
  <article class="partner-card">
    <div class="partner-logo"><span><i class="mark"></i>启明信贷中介协作会</span></div>
    <h3>启明信贷中介协作会</h3>
    <p>启明信贷中介协作会由多家信贷服务中介机构组成，旨在建立行业标准、加强信息共享、保护借贷双方权益，推动信贷服务中介行业健康有序发展，提升整体服务水平。</p>
  </article>

  <article class="partner-card">
    <div class="partner-logo"><span><i class="mark"></i>禾丰信用</span></div>
    <h3>北京禾丰信用评估有限公司</h3>
    <p>北京禾丰信用评估有限公司主要从事个人与企业信用信息服务，为网络借贷平台提供信用评估与风险提示支持。</p>
  </article>
  <article class="partner-card">
    <div class="partner-logo"><span><i class="mark"></i>明辉信用</span></div>
    <h3>上海明辉信用服务有限公司</h3>
    <p>上海明辉信用服务有限公司专注信用信息采集与评估，为金融机构提供专业、规范的信用报告服务。</p>
  </article>
  <article class="partner-card">
    <div class="partner-logo"><span><i class="mark"></i>远川律师事务所</span></div>
    <h3>远川律师事务所</h3>
    <p>远川律师事务所是一家综合性律师事务所，在金融与合同领域经验丰富，为本平台提供法律顾问服务。</p>
  </article>

  <article class="partner-card">
    <div class="partner-logo"><span><i class="mark"></i>Cirrovia</span></div>
    <h3>霁云科技</h3>
    <p>霁云科技是一家云计算服务提供商，为互联网企业提供服务器托管、运维管理与数据安全保障，确保平台稳定运行。</p>
  </article>
  <article class="partner-card">
    <div class="partner-logo"><span><i class="mark"></i>证鉴科技</span></div>
    <h3>北京证鉴科技有限公司</h3>
    <p>北京证鉴科技有限公司专注身份信息核查与验证服务，为金融机构提供实名认证及反欺诈支持。</p>
  </article>
  <article class="partner-card">
    <div class="partner-logo"><span><i class="mark"></i>衡付 Tallypay</span></div>
    <h3>衡付</h3>
    <p>衡付是一家第三方支付服务商，为用户提供安全便捷的在线支付、资金托管与结算服务。</p>
  </article>

  <article class="partner-card">
    <div class="partner-logo"><span><i class="mark"></i>澄付支付</span></div>
    <h3>澄付支付</h3>
    <p>澄付支付是持牌支付服务机构，提供网上支付、快捷支付及资金清算服务，保障用户资金安全流转。</p>
  </article>
  <article class="partner-card">
    <div class="partner-logo"><span><i class="mark"></i>华北数字商贸协会</span></div>
    <h3>华北数字商贸协会</h3>
    <p>华北数字商贸协会汇聚电商、支付与物流企业，推动行业交流、人才培养与规范发展。</p>
  </article>
</main>

<section class="news">
  <div class="news-col left">
    <h2>媒体报道</h2>
    <ul>
      <li class="on">这就是为什么人们选择这个平台</li>
      <li>这就是为什么人们选择这个平台</li>
      <li>这就是为什么人们选择这个简单的平台</li>
      <li>这就是为什么人们选择这个平台</li>
      <li>这就是为什么人们选择这个简单的例子</li>
    </ul>
    <span class="pill">更多&gt;</span>
  </div>
  <div class="news-col right">
    <h2>官方公告</h2>
    <ul>
      <li>这就是为什么人们选择这个平台</li>
      <li>这就是为什么人们选择这个简单的例子</li>
      <li>这就是为什么人们选择这个平台</li>
      <li>这就是为什么人们选择这个平台</li>
      <li>这就是为什么人们选择这个简单的例子</li>
    </ul>
    <span class="pill">更多&gt;</span>
  </div>
</section>

<section class="partner-strip">
  <h4>合作伙伴</h4>
  <div><span>Trenholt Capital</span><span>Cirrovia</span><span>小微信贷同业会</span><span>远川</span><span>禾丰信用</span><span>明辉信用</span></div>
</section>

<footer class="site-footer">
  <div class="row"><span>投资</span><span>贷款</span><span>安全</span><span>媒体</span><span>合作</span><span>关于我们</span><span>联系我们</span><span>加入我们</span><span>帮助中心</span></div>
  <div class="row"><span>友情链接：借贷观察</span><span>理财论坛</span><span>投资者社区</span></div>
  <div class="row"><span>客户服务：</span><i class="circle"></i><i class="circle"></i><i class="circle"></i><i class="circle"></i><span class="chat">在线客服</span></div>
  <div class="badges"><i></i><i></i><i></i><i></i><i></i><i></i></div>
  <div class="hotline"><small>客服电话</small><b>400-123-4567</b><small>周一至周五 9:00-18:00</small></div>
</footer>

<div class="copyright">
  <span>Copyright © 2014 Kelumo 京ICP备00000000号 | 版权所有 | 北京科乐信息技术有限公司</span>
  <div class="brand"><span class="dot"></span>Kelumo</div>
</div>
</body>
</html>
```